Stationery Design Project for Nimbora, Chicago

Nimbora, a street parking application which helps car drivers find a street parking spot by offering an ideal path along which to look for parking. This path is calculated by our algorithm based on data (e.g. historical data, baseball games schedule, etc.). Along this path the driver will find a spot and will also save 70% of the search time. Customer we target is reg. between 21 and 45 yo.

We envision something young, fresh, bright and original. Slightly abstract maybe. It should represent the idea and elements of finding street parking in the city, e.g. car(s), parking spot, people, city, etc. (just ideas!).

Logo is attached.

Requirement:
- Business Cards (2 Sided Full Color CMYK)
- Letterhead (1 Sided Full Color CMYK)
- Envelope (1 Sided Full Color CMYK)
- Sticker (1 Sided Full Color CMYK), round with a 2inch diameter.

Reason: We're starting to get more and more designs and need more time to look into all of them. Very exciting!! Thanks to everybody!

Hi all, we're in the process of selecting our favs. Though choices!!! Really good submissions. Will keep you posted and sorry for the delay.

Target Market(s)

Car drivers and owners between 21 and 45

Industry/Entity Type

Parking

Requirements
Must have
• Sticker should be round and include company URL nimbora.com and the new logo which we will attach soon.
Should not have
• Should not be too serious or boring.

```html
<!DOCTYPE html>
<html lang="en">
<head>
<meta charset="utf-8">
<title>Nimbora business card, front and back</title>
<link rel="stylesheet" href="https://fonts.googleapis.com/css2?family=Source+Sans+3:wght@400;600;700&display=swap">
<style>
  :root {
    --backdrop: #d9dadc;
    --card-blue-deep: #1d3a9e;
    --card-blue-mid: #1560c2;
    --card-blue-bright: #1f86dc;
    --divider-blue: #2c7fd6;
    --mark-circle: #2370d0;
    --paper: #ffffff;
    --ink-dark: #1a1a1a;
    --ink-grey: #555759;
    --ink-white: #ffffff;
  }
  * { margin: 0; padding: 0; box-sizing: border-box; }
  html, body {
    width: 954px; height: 1200px; overflow: hidden;
    background: var(--backdrop);
    font-family: "Source Sans 3", "Myriad Pro", sans-serif;
  }
  .canvas { position: relative; width: 954px; height: 1200px; }

  .card {
    position: absolute; left: 90px; width: 797px; height: 454px;
    border-radius: 28px; overflow: hidden;
    box-shadow: 0 6px 14px rgba(0,0,0,0.35);
  }
  .card--front { top: 91px; background: var(--paper); }
  .card--back {
    top: 658px;
    background: radial-gradient(circle at 398px 170px, var(--card-blue-bright) 0, var(--card-blue-mid) 170px, var(--card-blue-deep) 330px);
  }

  .front-panel {
    position: absolute; left: 0; top: 0; width: 437px; height: 100%;
    background: radial-gradient(circle at 218px 170px, var(--card-blue-bright) 0, var(--card-blue-mid) 180px, var(--card-blue-deep) 360px);
  }
  .front-divider {
    position: absolute; left: 437px; top: 0; width: 6px; height: 100%;
    background: linear-gradient(90deg, var(--card-blue-deep), var(--divider-blue));
  }

  .brand-mark {
    position: absolute; border-radius: 50%;
    background: var(--mark-circle);
    display: flex; align-items: center; justify-content: center;
    color: var(--ink-white); font-weight: 600; font-size: 34px;
  }
  .front-panel .brand-mark { left: 93px; top: 46px; width: 250px; height: 250px; }
  .card--back .brand-mark { left: 270px; top: 26px; width: 256px; height: 256px; }

  .address {
    position: absolute; left: 0; width: 437px; top: 370px;
    text-align: center; color: var(--ink-white);
    font-size: 20px; line-height: 26px;
  }

  .wordmark {
    position: absolute; left: 470px; top: 20px;
    font-size: 66px; font-weight: 600; color: var(--ink-dark);
    letter-spacing: 1px;
  }
  .holder { position: absolute; left: 472px; top: 204px; color: var(--ink-grey); }
  .holder-name { font-size: 25px; font-weight: 700; line-height: 32px; }
  .holder-role { font-size: 19px; font-weight: 700; line-height: 24px; }

  .contacts {
    position: absolute; left: 470px; top: 296px; list-style: none;
    color: var(--ink-grey); font-size: 20px;
  }
  .contacts li { display: flex; align-items: center; height: 32px; }
  .contacts svg { width: 20px; height: 18px; margin-right: 12px; fill: var(--ink-grey); }

  .back-url {
    position: absolute; left: 0; width: 100%; top: 377px;
    text-align: center; color: var(--ink-white); font-size: 30px;
  }
</style>
</head>
<body>
<div class="canvas">

  <section class="card card--front">
    <div class="front-panel">
      <div class="brand-mark">Nimbora</div>
      <p class="address">City Name, Street Name<br>State Name, Country Code</p>
    </div>
    <div class="front-divider"></div>

    <h1 class="wordmark">Nimbora</h1>
    <div class="holder">
      <p class="holder-name">Your Name</p>
      <p class="holder-role">Designation</p>
    </div>
    <ul class="contacts">
      <li>
        <svg viewBox="0 0 20 18" aria-hidden="true"><path d="M2 5c0-2 4-3 8-3s8 1 8 3v2h-4V5H6v2H2z"/><rect x="4" y="8" width="12" height="8" rx="2"/></svg>
        123-456-7890
      </li>
      <li>
        <svg viewBox="0 0 20 18" aria-hidden="true"><rect x="5" y="1" width="10" height="5"/><rect x="2" y="6" width="16" height="8" rx="1"/><rect x="5" y="12" width="10" height="5"/></svg>
        123-456-7890
      </li>
      <li>
        <svg viewBox="0 0 20 18" aria-hidden="true"><path d="M3 4h14v11H3z M4 5l6 5 6-5" fill="none" stroke="#555759" stroke-width="1.6"/></svg>
        name@website.com
      </li>
      <li>
        <svg viewBox="0 0 20 18" aria-hidden="true"><circle cx="10" cy="9" r="7"/><path d="M3 9h14M10 2v14" stroke="#fff" stroke-width="1"/></svg>
        www.website.com
      </li>
    </ul>
  </section>

  <section class="card card--back">
    <div class="brand-mark">Nimbora</div>
    <p class="back-url">www.website.com</p>
  </section>

</div>
</body>
</html>
```